Tech business card design

We need an amazing business card design for our new business 'Pexla' a marketing tech startup based in Sydney, Australia. We provide an online marketplace for businesses to search and buy advertising media, connect with service providers and learn more about marketing. We wish to communicate 'cool tech', reliability and professionalism and design based around our logo.

Target Market(s)

Business Owners

Contact Information for Business Card

Name
Position
Email Address
Website
Phone Number

Font styles to use
Other font styles liked:
• Avenir & Avenir Next

Colors

Designer to choose colors to be used in the design.

```html
<!DOCTYPE html>
<html lang="en">
<head>
<meta charset="utf-8">
<title>Pexla Business Card</title>
<link href="https://fonts.googleapis.com/css2?family=Nunito+Sans:wght@400;700;900&display=swap" rel="stylesheet">
<style>
  :root {
    --backdrop: #2a2a2a;
    --navy: #0c1a4d;
    --navy-deep: #081238;
    --navy-light: #1c2d68;
    --ink: #14204f;
    --paper: #ffffff;
    --silver: #c9cbd6;
    --mist: #b8bfd6;
  }
  * { margin: 0; padding: 0; box-sizing: border-box; }
  html, body {
    width: 1200px;
    height: 876px;
    overflow: hidden;
    background: var(--backdrop);
    font-family: "Nunito Sans", Arial, sans-serif;
  }
  .stage {
    position: relative;
    width: 1200px;
    height: 876px;
  }
  .card {
    position: absolute;
    top: 290px;
    width: 520px;
    height: 297px;
    overflow: hidden;
    border-radius: 2px;
  }
  .card--front { left: 50px; background: var(--paper); }
  .card--back {
    left: 630px;
    background: var(--navy);
  }
  .wordmark {
    position: absolute;
    font-weight: 900;
    letter-spacing: -1px;
    line-height: 1;
  }
  .card--front .wordmark {
    left: 0; right: 0;
    top: 100px;
    text-align: center;
    font-size: 76px;
    color: var(--ink);
  }
  .front-band {
    position: absolute;
    left: 0; bottom: 0;
    width: 100%;
    height: 90px;
  }
  .front-web {
    position: absolute;
    left: 18px;
    bottom: 0;
    height: 24px;
    display: flex;
    align-items: center;
    font-size: 11px;
    line-height: 1;
    color: var(--paper);
    letter-spacing: 0.3px;
  }
  .back-glow {
    position: absolute;
    inset: 0;
    width: 100%;
    height: 100%;
  }
  .card--back .wordmark {
    left: 150px;
    top: 58px;
    font-size: 84px;
    color: var(--paper);
  }
  .holder {
    position: absolute;
    left: 150px;
    top: 160px;
    color: var(--paper);
  }
  .holder__name {
    font-weight: 700;
    font-size: 20px;
    line-height: 1.2;
    letter-spacing: 1px;
    text-transform: uppercase;
  }
  .holder__role {
    font-size: 13px;
    line-height: 1.3;
    color: var(--mist);
    letter-spacing: 0.4px;
  }
  .contacts {
    position: absolute;
    left: 18px;
    right: 18px;
    bottom: 16px;
    display: flex;
    gap: 14px;
    font-size: 12px;
    line-height: 1.2;
    color: var(--paper);
  }
  .contacts__item {
    display: flex;
    align-items: center;
    gap: 5px;
  }
  .contacts__icon { width: 11px; height: 11px; fill: var(--paper); }
</style>
</head>
<body>
<main class="stage">

  <section class="card card--front" aria-label="Card front">
    <div class="wordmark">pexla</div>
    <svg class="front-band" viewBox="0 0 520 90" preserveAspectRatio="none" aria-hidden="true">
      <path d="M0 62 L300 62 Q312 62 318 54 L328 40 Q334 32 346 32 L520 32 L520 90 L0 90 Z" fill="var(--silver)"/>
      <path d="M0 66 L306 66 Q318 66 324 58 L334 46 Q340 38 352 38 L520 38 L520 90 L0 90 Z" fill="var(--navy-deep)"/>
    </svg>
    <div class="front-web">www.pexlamail.com</div>
  </section>

  <section class="card card--back" aria-label="Card back">
    <svg class="back-glow" viewBox="0 0 520 297" preserveAspectRatio="none" aria-hidden="true">
      <defs>
        <linearGradient id="arcShade" x1="0" y1="0" x2="1" y2="1">
          <stop offset="0" stop-color="var(--navy-light)"/>
          <stop offset="1" stop-color="var(--navy)"/>
        </linearGradient>
      </defs>
      <path d="M0 0 L60 0 Q380 40 470 297 L0 297 Z" fill="url(#arcShade)"/>
    </svg>
    <div class="wordmark">pexla</div>
    <div class="holder">
      <div class="holder__name">Marcus Reed</div>
      <div class="holder__role">Managing Director</div>
    </div>
    <div class="contacts">
      <span class="contacts__item">
        <svg class="contacts__icon" viewBox="0 0 12 12" aria-hidden="true"><path d="M2.5 0.5 L4.5 3 L3.5 4.5 Q4.5 7 7.5 8.5 L9 7.5 L11.5 9.5 L10 11.5 Q4 11 0.5 2 Z"/></svg>
        000-555-0192
      </span>
      <span class="contacts__item">
        <svg class="contacts__icon" viewBox="0 0 12 12" aria-hidden="true"><path d="M0.5 2 H11.5 V10 H0.5 Z M1.5 3 L6 6.5 L10.5 3" fill="none" stroke="var(--paper)" stroke-width="1.2"/></svg>
        info@pexlamail.com
      </span>
      <span class="contacts__item">
        <svg class="contacts__icon" viewBox="0 0 12 12" aria-hidden="true"><g fill="none" stroke="var(--paper)" stroke-width="1"><circle cx="6" cy="6" r="5"/><ellipse cx="6" cy="6" rx="2.2" ry="5"/><path d="M1 6 H11"/></g></svg>
        www.pexlamail.com
      </span>
    </div>
  </section>

</main>
</body>
</html>
```